Ward Compass Business Card Design*

We need a business card design for our company Ward Compass. Our company is specialized in providing online consulting services regarding medical institutions, hospitals and doctors. We work with patients worldwide looking to choose between healthcare providers. We have a website you may use as a reference, where we list doctors and clinics worldwide. So we target Medical providers as well as patients worldwide.
Target Market(s)
Medical Providers and patients around the world
Industry/Entity Type
Medical
Contact Information for Business Card
Salwa Kettani
CEO
+90 612 348 2175
info@wardcompass.example
www.wardcompass.example
14 Annakhil 7 H.R.B. Rabat, Morocco
Requirements
Must have
- Company logo/name on one full side, personal info and smaller logo and company name on the other side.
Nice to have
- Smart and elegant design

```html
<!DOCTYPE html>
<html lang="en">
<head>
<meta charset="utf-8">
<title>Ward Compass Business Card</title>
<link rel="stylesheet" href="https://fonts.googleapis.com/css2?family=Montserrat:wght@500;600&family=Arimo:wght@400;700&display=swap">
<style>
  :root {
    --page: #d9d4cd;
    --card-light: #f1f0ee;
    --card-mid: #e2e0dd;
    --navy: #262f4d;
    --charcoal: #34302f;
    --ink: #2b3348;
    --ink-soft: #5a5f6b;
  }
  html, body {
    margin: 0;
    width: 1200px;
    height: 970px;
    overflow: hidden;
    background: var(--page);
  }
  .stage {
    width: 1200px;
    height: 970px;
    display: flex;
    align-items: center;
    justify-content: center;
  }
  .business-card {
    display: block;
    width: 1040px;
    height: 606px;
    box-shadow: 0 18px 40px rgba(40, 35, 30, 0.25);
  }
  .wordmark {
    font-family: "Montserrat", sans-serif;
    font-weight: 600;
    font-size: 40px;
    letter-spacing: 1px;
    fill: var(--ink);
  }
  .person-name {
    font-family: "Arimo", sans-serif;
    font-size: 28px;
    fill: var(--ink);
  }
  .person-name .first { font-weight: 700; }
  .person-name .last { font-weight: 400; fill: var(--ink-soft); }
  .person-role {
    font-family: "Arimo", sans-serif;
    font-size: 21px;
    fill: var(--ink-soft);
  }
  .contact-line {
    font-family: "Arimo", sans-serif;
    font-size: 22px;
    fill: var(--ink-soft);
  }
  .icon-disc { fill: var(--navy); }
  .icon-glyph { fill: none; stroke: #ffffff; stroke-width: 1.6; stroke-linecap: round; stroke-linejoin: round; }
</style>
</head>
<body>
<main class="stage">
  <svg class="business-card" viewBox="0 0 1013 590" xmlns="http://www.w3.org/2000/svg" aria-label="Ward Compass business card, front">
    <defs>
      <linearGradient id="card-face" x1="0" y1="0" x2="1" y2="1">
        <stop offset="0" stop-color="var(--card-light)"/>
        <stop offset="1" stop-color="var(--card-mid)"/>
      </linearGradient>
    </defs>

    <rect class="card-face" width="1013" height="590" fill="url(#card-face)"/>
    <path class="band-navy" d="M0,0 H1013 V14 C700,22 260,90 0,290 Z" fill="var(--navy)"/>
    <path class="band-charcoal" d="M1013,268 C900,460 520,568 0,572 V590 H1013 Z" fill="var(--charcoal)"/>

    <g class="brand">
      <circle cx="525" cy="160" r="26" fill="var(--navy)"/>
      <text class="wordmark" x="572" y="175">WARD COMPASS</text>
    </g>

    <g class="person">
      <text class="person-name" x="64" y="368"><tspan class="first">SALWA</tspan> <tspan class="last">KETTANI</tspan></text>
      <text class="person-role" x="64" y="399">CEO</text>
    </g>

    <g class="contacts">
      <g class="contact phone">
        <circle class="icon-disc" cx="76" cy="450" r="12"/>
        <path class="icon-glyph" d="M72,444 l2.5,-1 l2,4 l-1.8,1.4 q1.5,3 4,4.5 l1.6,-1.7 l3.8,2.2 l-1,2.4 q-6,0.5 -10.6,-7.6 q-1.5,-2.7 -0.5,-4.2 z"/>
        <text class="contact-line" x="106" y="458">+90 612 348 2175</text>
      </g>
      <g class="contact email">
        <circle class="icon-disc" cx="76" cy="486" r="12"/>
        <rect class="icon-glyph" x="69" y="481" width="14" height="10" rx="1"/>
        <path class="icon-glyph" d="M69,482 L76,487.5 L83,482"/>
        <text class="contact-line" x="106" y="494">info@wardcompass.example</text>
      </g>
      <g class="contact web">
        <circle class="icon-disc" cx="76" cy="521" r="12"/>
        <circle class="icon-glyph" cx="76" cy="521" r="7"/>
        <ellipse class="icon-glyph" cx="76" cy="521" rx="3" ry="7"/>
        <path class="icon-glyph" d="M69,521 H83"/>
        <text class="contact-line" x="106" y="529">www.wardcompass.example</text>
      </g>
    </g>
  </svg>
</main>
</body>
</html>
```